Tech business card design

We need an amazing business card design for our new business 'Pexla' a marketing tech startup based in Sydney, Australia. We provide an online marketplace for businesses to search and buy advertising media, connect with service providers and learn more about marketing. We wish to communicate 'cool tech', reliability and professionalism and design based around our logo.

Target Market(s)

Business Owners

Contact Information for Business Card

Name
Position
Email Address
Website
Phone Number

Font styles to use
Other font styles liked:
• Avenir & Avenir Next

Colors

Designer to choose colors to be used in the design.

```html
<!DOCTYPE html>
<html lang="en">
<head>
<meta charset="utf-8">
<title>Pexla Business Card</title>
<link href="https://fonts.googleapis.com/css2?family=Nunito+Sans:wght@400;600;800;900&display=swap" rel="stylesheet">
<style>
  :root {
    --stage: #2b2b2b;
    --navy: #0b1a4a;
    --navy-map: #1a2b62;
    --paper: #f7f7f8;
    --ink: #0f1c4d;
    --muted: #5a5f6e;
    --rule: #d6d8de;
    --band-edge: #c9ccd8;
  }
  * { margin: 0; padding: 0; box-sizing: border-box; }
  html, body { width: 1200px; height: 907px; overflow: hidden; }
  body {
    background: var(--stage);
    font-family: "Nunito Sans", "Helvetica Neue", Arial, sans-serif;
    position: relative;
  }
  .card {
    position: absolute;
    top: 303px;
    width: 520px;
    height: 300px;
    box-shadow: 0 10px 30px rgba(0,0,0,0.45);
    overflow: hidden;
  }
  /* Back */
  .card-back { left: 50px; background: var(--navy); }
  .world-map {
    position: absolute;
    left: 40px; top: 40px; width: 440px; height: 200px;
    background: radial-gradient(ellipse at center, var(--navy-map) 0%, rgba(26,43,98,0.4) 55%, rgba(11,26,74,0) 80%);
  }
  .card-back .brand {
    position: absolute;
    left: 0; right: 0; top: 100px;
    text-align: center;
    font-weight: 900;
    font-size: 76px;
    letter-spacing: -2px;
    color: #ffffff;
    line-height: 1;
  }
  .card-back .site {
    position: absolute;
    left: 0; right: 0; top: 214px;
    text-align: center;
    font-size: 14px;
    letter-spacing: 1px;
    color: #b8bfd6;
  }
  /* Front */
  .card-front { left: 630px; background: var(--paper); }
  .card-front .brand {
    position: absolute;
    left: 32px; top: 88px;
    font-weight: 900;
    font-size: 74px;
    letter-spacing: -2px;
    color: var(--ink);
    line-height: 1;
  }
  .divider {
    position: absolute;
    left: 292px; top: 36px;
    width: 1px; height: 180px;
    background: var(--rule);
  }
  .details { position: absolute; left: 314px; top: 42px; }
  .person-name {
    font-weight: 800;
    font-size: 19px;
    letter-spacing: 0.5px;
    color: var(--ink);
    text-transform: uppercase;
  }
  .person-role {
    font-size: 13px;
    color: var(--muted);
    margin-top: 2px;
  }
  .contact-list { list-style: none; margin-top: 30px; }
  .contact-list li {
    display: flex; align-items: center;
    font-size: 13px;
    color: var(--muted);
    line-height: 22px;
  }
  .contact-list svg { width: 12px; height: 12px; margin-right: 9px; fill: var(--ink); flex: none; }
  .band {
    position: absolute;
    left: 0; right: 0; bottom: 0;
    height: 40px;
    background: var(--navy);
    border-top: 4px solid var(--band-edge);
  }
</style>
</head>
<body>
  <section class="card card-back">
    <div class="world-map" role="img" aria-label="Faint dotted world map backdrop"></div>
    <div class="brand">pexla</div>
    <div class="site">www.pexla.com</div>
  </section>

  <section class="card card-front">
    <div class="brand">pexla</div>
    <div class="divider"></div>
    <div class="details">
      <div class="person-name">Marcus Reed</div>
      <div class="person-role">Managing Director</div>
      <ul class="contact-list">
        <li>
          <svg viewBox="0 0 12 12" aria-hidden="true"><path d="M1 4 Q6 0 11 4 L10 5.5 L8 4.5 L8 3.5 Q6 3 4 3.5 L4 4.5 L2 5.5 Z M3 6 H9 L10 11 H2 Z"/></svg>
          000-482-7190
        </li>
        <li>
          <svg viewBox="0 0 12 12" aria-hidden="true"><path d="M1 2.5 H11 V9.5 H1 Z M1.5 3 L6 6.5 L10.5 3" stroke="#f7f7f8" stroke-width="0.8"/></svg>
          info@pexla.com
        </li>
        <li>
          <svg viewBox="0 0 12 12" aria-hidden="true"><circle cx="6" cy="6" r="5.5"/><path d="M0.5 6 H11.5 M6 0.5 V11.5 M6 0.5 Q2.5 6 6 11.5 M6 0.5 Q9.5 6 6 11.5" stroke="#f7f7f8" stroke-width="0.7" fill="none"/></svg>
          www.pexla.com
        </li>
      </ul>
    </div>
    <div class="band"></div>
  </section>
</body>
</html>
```